Want to go online this week, rush project, everything is there, just make it pretty

I need a pretty html5/css template for a already made site. Please do not rearrange anything unless you feel you can simplify the design. I have a raw site. Please play with the site by making an account with coupon code BRIGHTPEARL for free signup. Log in, log out, download as many designs as you can, then log in and log out. See everything cause it's brand new and I need it neat and pretty over the next few days if not sooner. So, after all that, the site is http://StitchLoomPatternsHub.example
Updates

Project Deadline Extended
Reason: Extending until the 30th to give more time.

Is anyone working on something to submit? If you have something please submit asap as I will be closing this Sat night or Sunday morning

Industry/Entity Type

Online

Coding

Coded - Design and coding required

```html
<!DOCTYPE html>
<html lang="en">
<head>
<meta charset="utf-8">
<title>Stitch Loom Patterns Hub</title>
<link href="https://fonts.googleapis.com/css2?family=Open+Sans:wght@400;600&family=Roboto:wght@400;500&family=Oswald:wght@500&display=swap" rel="stylesheet">
<style>
:root{
  --pink:#f0569a;
  --pink-soft:#f47ab3;
  --green:#86c15a;
  --green-dark:#74ad4a;
  --text:#555;
  --muted:#777;
  --line:#e6e6e6;
  --panel:#f6f6f4;
  --white:#fff;
}
*{box-sizing:border-box;margin:0;padding:0}
html,body{width:821px;height:1200px;overflow:hidden;background:var(--white)}
body{position:relative;font-family:"Open Sans",sans-serif;color:var(--text)}
.abs{position:absolute}
.site-stats{left:118px;top:58px;display:flex;align-items:center;gap:12px;font-size:8.5px;line-height:15px}
.stats-icon{width:26px;height:26px;border-radius:50%;border:2px solid #bbb}
.brand{left:312px;top:28px;width:196px;height:94px;display:flex;flex-direction:column;align-items:center;justify-content:center}
.brand-name{font-family:"Roboto",sans-serif;font-weight:500;font-size:22px;color:var(--pink);line-height:24px}
.brand-sub{font-family:"Roboto",sans-serif;font-weight:500;font-size:11px;color:var(--pink);}
.brand-dot{width:10px;height:10px;border-radius:50%;background:var(--green);margin-bottom:6px}
.notify{left:534px;top:58px;display:flex;align-items:center;gap:14px;font-size:8.5px;line-height:15px}
.notify-icon{width:40px;height:18px;border-radius:5px;background:#7b4a8c}
.divider{left:88px;top:141px;width:646px;border-top:1px dashed #f2a7c8}
.sidebar{left:88px;top:153px;width:148px}
.sidebar-title{height:35px;background:var(--pink);color:#fff;font-family:"Roboto",sans-serif;font-size:14.5px;padding:8px 10px}
.cat-list{list-style:none;background:var(--panel);border:1px solid #eee;border-top:0}
.cat-list li{height:23.5px;border-bottom:1px solid var(--line);font-size:8.3px;display:flex;align-items:center;padding-left:27px;position:relative}
.cat-list li::before{content:"";position:absolute;left:10px;top:8px;width:7px;height:7px;border-radius:50%;background:var(--pink)}
.promo{left:87px;width:149px;display:flex;flex-direction:column;align-items:center;justify-content:center;font-family:"Oswald",sans-serif;text-transform:uppercase;line-height:1.2}
.promo-register{top:680px;height:119px;background:var(--pink-soft);color:#fff;font-size:17px}
.promo-register .small{font-size:14px}
.promo-dvd{top:815px;height:119px;background:#ececec;color:var(--pink);font-size:15.5px;align-items:flex-start;padding-left:26px}
.promo-disc{position:absolute;right:0;top:14px;width:46px;height:92px;border-radius:92px 0 0 92px;background:#d9d9d9}
.main-nav{left:254px;top:153px;width:480px;height:35px;background:var(--green);display:flex;align-items:center;padding-left:18px;font-family:"Roboto",sans-serif;font-size:10.5px;color:#fff}
.main-nav span.sep{margin:0 13px}
.hero{left:254px;top:201px;width:480px;height:262px;background:linear-gradient(135deg,#c9cfae,#b8bf98);box-shadow:0 3px 5px rgba(0,0,0,.15)}
.hero-art{position:absolute;right:0;top:0;width:230px;height:262px;background:radial-gradient(circle at 55% 55%,#8a4e8c 0,#a2a57a 70%)}
.hero-title{position:absolute;left:30px;top:60px;font-family:"Oswald",sans-serif;font-size:25px;color:#e2643a;line-height:38px;letter-spacing:1px}
.hero-btn{position:absolute;left:30px;top:143px;height:29px;padding:0 18px;background:#2b2b2b;color:#fff;font-family:"Roboto",sans-serif;font-size:13px;display:flex;align-items:center;border-radius:2px}
.hero-arrows{position:absolute;left:30px;top:186px;display:flex;gap:6px}
.hero-arrows svg{width:23px;height:23px}
.card{width:147px;height:216px;background:#fff;border:1px solid #eee}
.card-img{height:107px}
.view-tag{position:absolute;left:32px;top:92px;width:83px;height:19px;background:#fff;box-shadow:0 1px 3px rgba(0,0,0,.15);font-family:"Roboto",sans-serif;font-size:8.5px;color:var(--pink);display:flex;align-items:center;gap:14px;padding-left:8px}
.view-tag i{width:11px;height:9px;background:repeating-linear-gradient(90deg,#bbb 0 3px,transparent 3px 4px)}
.card-title{position:absolute;top:127px;width:100%;text-align:center;font-family:"Roboto",sans-serif;font-size:11px;color:#444}
.card-meta{position:absolute;top:153px;width:100%;text-align:center;font-size:8px;line-height:13px;color:var(--muted)}
.card-btn{position:absolute;left:0;bottom:0;width:100%;height:30px;background:var(--green);color:#fff;font-family:"Roboto",sans-serif;font-weight:500;font-size:10.5px;display:flex;align-items:center;justify-content:center}
.pager{left:341px;top:961px;display:flex;gap:6px}
.pager span{height:18px;min-width:18px;padding:0 6px;border:1px solid #ddd;font-size:8px;font-weight:600;display:flex;align-items:center;justify-content:center;color:#444}
.pager .wide{padding:0 9px}
.footer{left:88px;top:1005px;width:646px;height:146px;background:#f8f8f8;border:1px solid #eee}
.f-col{position:absolute;top:18px}
.f-col h4{font-family:"Roboto",sans-serif;font-weight:400;font-size:9.5px;color:var(--pink);margin-bottom:10px}
.f-col ul{list-style:none;font-size:7.5px;line-height:14px;color:#666}
.f-rule{position:absolute;top:12px;width:1px;height:120px;background:#e8e8e8}
.news{width:142px;height:22px;background:#fff;border:1px solid #e5e5e5;font-size:9px;text-align:right;padding:3px 8px}
.social{display:flex;gap:7px}
.social span{width:22px;height:22px;border-radius:50%;background:var(--pink)}
.copy{left:91px;top:1171px;font-size:7.5px;color:var(--pink)}
.legal{right:87px;top:1172px;font-size:7.5px;color:#444}
</style>
</head>
<body>

<div class="abs site-stats">
  <div class="stats-icon"></div>
  <div>27,906 unique designs online<br>1,982 design sets/packs</div>
</div>

<div class="abs brand">
  <div class="brand-dot"></div>
  <div class="brand-name">StitchLoom</div>
  <div class="brand-sub">PatternsHub.example</div>
</div>

<div class="abs notify">
  <div class="notify-icon" role="img" aria-label="Small classic car illustration"></div>
  <div>Get notified of new designs!<br>&nbsp;Today's Free Design</div>
</div>

<div class="abs divider"></div>

<aside class="abs sidebar">
  <div class="sidebar-title">Categories</div>
  <ul class="cat-list">
    <li>Filled Design, Bear</li><li>Halloween</li><li>Animal, Hoops &amp; Frames</li><li>Icons-Signs-Symbols</li>
    <li>Flowers and Plants</li><li>Household Items</li><li>Objects &amp; Things</li><li>Bindings, Cords &amp; Elastics</li>
    <li>Machine Embroidery</li><li>Buttons and Buckles</li><li>Crafts, Lighting</li><li>Dressmaking &amp; Tailoring</li>
    <li>Fabrics-&gt;</li><li>Haberdashery</li><li>Bindings, Cords &amp; Elastics</li><li>Books</li>
    <li>Buttons and Buckles</li><li>Transportation</li><li>Dressmaking &amp; Tailoring</li><li>Objects &amp; Things</li>
  </ul>
</aside>

<div class="abs promo promo-register">
  <div>Register</div><div class="small">For Unlimited</div><div class="small">Embroidery Design</div><div>Downloads!</div>
</div>
<div class="abs promo promo-dvd">
  <div class="promo-disc" role="img" aria-label="Disc illustration"></div>
  <div>Get all</div><div>Designs</div><div>on DVD</div><div>Coming soon</div>
</div>

<nav class="abs main-nav">
  Home<span class="sep">/</span>Register<span class="sep">/</span>Account<span class="sep">/</span>Contact<span class="sep">/</span>Search<span class="sep">/</span>Bookmark
</nav>

<section class="abs hero">
  <div class="hero-art" role="img" aria-label="Photo of purple and yellow flower embroidery on linen"></div>
  <div class="hero-title">EMBROIDERY<br>DESIGN</div>
  <div class="hero-btn">Register Now</div>
  <div class="hero-arrows">
    <svg viewBox="0 0 24 24"><circle cx="12" cy="12" r="12" fill="#777" opacity=".8"/><path d="M14 7l-5 5 5 5" stroke="#fff" stroke-width="2" fill="none"/></svg>
    <svg viewBox="0 0 24 24"><circle cx="12" cy="12" r="12" fill="#777" opacity=".8"/><path d="M10 7l5 5-5 5" stroke="#fff" stroke-width="2" fill="none"/></svg>
  </div>
</section>

<article class="abs card" style="left:254px;top:485px">
  <div class="card-img" role="img" aria-label="Embroidery of a man beside a red car" style="background:linear-gradient(90deg,#c9333b,#3e4aa0)"></div>
  <div class="view-tag"><i></i>VIEW SET</div>
  <div class="card-title">Muscle Cars 2</div>
  <div class="card-meta">10 Designs<br>All Fit the 4x4 Hoop</div>
  <div class="card-btn">DOWNLOAD NOW</div>
</article>
<article class="abs card" style="left:420px;top:485px">
  <div class="card-img" role="img" aria-label="Green applique monster embroidery" style="background:linear-gradient(#d9e6cf,#6cc23a)"></div>
  <div class="view-tag"><i></i>VIEW SET</div>
  <div class="card-title">Cute Applique Monsters</div>
  <div class="card-meta">10 Designs<br>All Fit the 4x4 Hoop</div>
  <div class="card-btn">DOWNLOAD NOW</div>
</article>
<article class="abs card" style="left:587px;top:485px">
  <div class="card-img" role="img" aria-label="Swirly cat face embroidery" style="background:linear-gradient(#eef1f4,#e8b9a0)"></div>
  <div class="view-tag"><i></i>VIEW SET</div>
  <div class="card-title">Swirly Cat Faces 2</div>
  <div class="card-meta">10 Designs<br>All Fit the 4x4 Hoop</div>
  <div class="card-btn">DOWNLOAD NOW</div>
</article>

<article class="abs card" style="left:254px;top:719px">
  <div class="card-img" role="img" aria-label="Black bat embroidery" style="background:radial-gradient(circle,#333 0,#ebe3d6 60%)"></div>
  <div class="view-tag"><i></i>VIEW SET</div>
  <div class="card-title">Halloween Cuties</div>
  <div class="card-meta">10 Designs<br>All Fit the 4x4 Hoop</div>
  <div class="card-btn">DOWNLOAD NOW</div>
</article>
<article class="abs card" style="left:420px;top:719px">
  <div class="card-img" role="img" aria-label="Gold tiara embroidery" style="background:radial-gradient(circle,#e4c98a 0,#f1efe9 60%)"></div>
  <div class="view-tag"><i></i>VIEW SET</div>
  <div class="card-title">Tiaras</div>
  <div class="card-meta">10 Designs<br>All Fit the 4x4 Hoop</div>
  <div class="card-btn">DOWNLOAD NOW</div>
</article>
<article class="abs card" style="left:587px;top:719px">
  <div class="card-img" role="img" aria-label="Bear in pumpkin costume embroidery" style="background:radial-gradient(circle,#c8583a 0,#e5e8ee 65%)"></div>
  <div class="view-tag"><i></i>VIEW SET</div>
  <div class="card-title">Not So Scary Bears</div>
  <div class="card-meta">10 Designs<br>All Fit the 4x4 Hoop</div>
  <div class="card-btn">DOWNLOAD NOW</div>
</article>

<div class="abs pager">
  <span class="wide">Prev</span><span>1</span><span>2</span><span>3</span><span>4</span><span>5</span><span>6</span><span>...</span><span>22</span><span class="wide">Next</span>
</div>

<footer class="abs footer">
  <div class="f-col" style="left:22px">
    <h4>INFORMATION</h4>
    <ul><li>Home</li><li>Register</li><li>Account</li><li>Contact</li><li>Search</li><li>Bookmark This Page</li></ul>
  </div>
  <div class="f-rule" style="left:133px"></div>
  <div class="f-col" style="left:168px">
    <h4>CATEGORIES</h4>
    <ul><li>Filled Design, Bear</li><li>Halloween</li><li>Animal, Hoops &amp; Frames</li><li>Icons-Signs-Symbols</li><li>Flowers and Plants</li><li>Household Items</li></ul>
  </div>
  <div class="f-col" style="left:314px;top:42px">
    <ul><li>Objects &amp; Things</li><li>Bindings, Cords &amp; Elastics</li><li>Machine Embroidery</li><li>Buttons and Buckles</li><li>Crafts, Lighting</li><li>Dressmaking &amp; Tailoring</li></ul>
  </div>
  <div class="f-rule" style="left:447px"></div>
  <div class="f-col" style="left:484px">
    <h4>NEWSLETTER</h4>
    <div class="news">›</div>
  </div>
  <div class="f-col" style="left:482px;top:74px">
    <h4>FOLLOW US</h4>
    <div class="social"><span></span><span></span><span></span></div>
  </div>
</footer>

<div class="abs copy">©2013 - 2014 Stitch Loom Designs., All Rights Reserved.</div>
<div class="abs legal">Terms of Service | Privacy Policy</div>

</body>
</html>
```